Stationary Set Rebrand for Brennick

We are a Canadian Distribution and Service Company that was established in 1969. Over the past 5 decades we have expanded our business and have warehouses across Canada. We specialize in adhesive tapes, adhesives, films, safety, warehouse, shipping, janitorial and packaging supplies.

We have updated our logo design and would like a new corporate branding identity that includes a new fresh Stationary Set (Business Cards, Letterhead, Letterhead MS Word, Envelope, Presentation Folders, Email Signatures, Notepad Covers, etc.)

Target Market(s)

Industrial Business Sector

Font styles to use
Sans Serif

Colors
0054AA
0677BA
7BADD7
CADEEF
E8F1F8
0094D4
00A9DD
6FCCEA
C7EBF8
E9F6FB
00AB8E
00BBA5
67D7C9
C6EFE9
E9F9F6
EB3D1F
EC4F4E
F09395
F8D3D4
FCEDEE

Requirements
Should not have
• Colors not too light, darker colours preferred

```html
<!DOCTYPE html>
<html lang="en">
<head>
<meta charset="utf-8">
<title>Brennick Business Card</title>
<link href="https://fonts.googleapis.com/css2?family=Krona+One&family=Rajdhani:wght@500;700&display=swap" rel="stylesheet">
<style>
  :root {
    --bg: #dcdcdc;
    --card-white: #ffffff;
    --card-dark: #303030;
    --brand-red: #d7161f;
    --ink: #1d1d1d;
    --text-grey: #4a4a4a;
    --rule-grey: #b5b5b5;
  }
  * { margin: 0; padding: 0; box-sizing: border-box; }
  html, body {
    width: 1200px;
    height: 1200px;
    overflow: hidden;
    background: var(--bg);
  }
  .canvas {
    position: relative;
    width: 1200px;
    height: 1200px;
  }
  .card {
    position: absolute;
    width: 696px;
    height: 398px;
  }
  .card-front {
    left: 262px;
    top: 156px;
    background: var(--card-white);
  }
  .card-back {
    left: 258px;
    top: 652px;
    background: var(--card-dark);
    display: flex;
    align-items: center;
    justify-content: center;
  }
  .brand-name {
    position: absolute;
    right: 53px;
    top: 38px;
    font-family: "Rajdhani", sans-serif;
    font-weight: 700;
    font-size: 74px;
    line-height: 1;
    color: var(--ink);
  }
  .holder-name {
    position: absolute;
    left: 48px;
    top: 227px;
    font-family: "Krona One", sans-serif;
    font-size: 21px;
    line-height: 1;
    color: var(--brand-red);
  }
  .holder-title {
    position: absolute;
    left: 49px;
    top: 254px;
    font-family: "Rajdhani", sans-serif;
    font-weight: 500;
    font-size: 16px;
    letter-spacing: 0.5px;
    color: var(--text-grey);
  }
  .divider {
    position: absolute;
    left: 50px;
    top: 284px;
    width: 598px;
    height: 1px;
    background: var(--rule-grey);
  }
  .contact-list {
    position: absolute;
    left: 47px;
    top: 292px;
    list-style: none;
    font-family: "Rajdhani", sans-serif;
    font-weight: 500;
    font-size: 18px;
    letter-spacing: 0.4px;
    color: var(--text-grey);
  }
  .contact-list li {
    display: flex;
    align-items: center;
    height: 20.8px;
  }
  .contact-icon {
    width: 16px;
    height: 16px;
    margin-right: 8px;
    fill: var(--brand-red);
  }
  .address {
    position: absolute;
    right: 43px;
    top: 294px;
    text-align: right;
    font-family: "Rajdhani", sans-serif;
    font-weight: 500;
    font-size: 18px;
    line-height: 20.8px;
    letter-spacing: 0.4px;
    color: var(--text-grey);
  }
  .edge-line {
    position: absolute;
    left: 0;
    top: 375px;
    width: 100%;
    height: 3px;
    background: var(--ink);
  }
  .edge-band {
    position: absolute;
    left: 0;
    bottom: 0;
    width: 100%;
    height: 17px;
    background: var(--brand-red);
  }
  .back-brand {
    font-family: "Rajdhani", sans-serif;
    font-weight: 700;
    font-size: 82px;
    line-height: 1;
    color: var(--brand-red);
  }
</style>
</head>
<body>
<main class="canvas">
  <section class="card card-front">
    <div class="brand-name">Brennick</div>
    <h1 class="holder-name">DANA MERCER</h1>
    <p class="holder-title">President</p>
    <div class="divider"></div>
    <ul class="contact-list">
      <li>
        <svg class="contact-icon" viewBox="0 0 16 16" aria-hidden="true"><path d="M3.2 1.2l2.4-.4 1.5 3.4-1.6 1.2c.8 1.8 2.2 3.3 4 4.2l1.3-1.5 3.4 1.6-.5 2.5c-.2.8-1 1.3-1.8 1.2C6.4 12.8 2.6 8.6 2 3c-.1-.8.4-1.6 1.2-1.8z"/></svg>
        <span>604-218-7730</span>
      </li>
      <li>
        <svg class="contact-icon" viewBox="0 0 16 16" aria-hidden="true"><path d="M4.5 0h7A1.5 1.5 0 0 1 13 1.5v13a1.5 1.5 0 0 1-1.5 1.5h-7A1.5 1.5 0 0 1 3 14.5v-13A1.5 1.5 0 0 1 4.5 0zM4.6 2v10.4h6.8V2zM7 13.4v1.2h2v-1.2z"/></svg>
        <span>604-219-4412</span>
      </li>
      <li>
        <svg class="contact-icon" viewBox="0 0 16 16" aria-hidden="true"><path d="M1 3.5h14v1L8 9 1 4.5zM1 6l7 4.5L15 6v6.5H1z"/></svg>
        <span>info@brennick.com</span>
      </li>
    </ul>
    <address class="address" style="font-style: normal;">
      412 Cedarvale Road<br>
      Kingsford, Canada 20418<br>
      www.brennick.com
    </address>
    <div class="edge-line"></div>
    <div class="edge-band"></div>
  </section>

  <section class="card card-back">
    <div class="back-brand">Brennick</div>
  </section>
</main>
</body>
</html>
```